High-end construction company needs a business card design

We need a modern looking business card that draws people in, is memorable and looks so good people will want to sick it on their fridges.
On the first side what is needed are:
Logo
My name - Tomasz Brelwik
Title - Managing Director
Website - www.varkelt.co.uk
Email - tomasz@varkelt.co.uk
Telephone - 020 5194 6281
Mobile - 07845139072
On the back side was is needed is a list of all the services we provide:
-Kitchen Renovations
-Bathroom Renovations
-House Renovations
-Garage Conversions
-Extensions
-Loft Conversions
-Conservatories
-Carpentry
-Tiling
-Electrical
-Plumbing & Heating
-Bricklaying
-Landscaping
-Decorating
-Plastering
We would like the colours to be the same shades as on the logo with grey or black for the words.
Target Market(s)
Anyone who needs building work done
Contact Information for Business Card
This business card is for a construction company which strives to deliver excellent service and quality.
The look and feel of the card should represent this.
Requirements
Must have
- On the first side what is needed are:
Logo
My name - Tomasz Brelwik
Title - Managing Director
Website - www.varkelt.co.uk
Email - tomasz@varkelt.co.uk
Telephone - 020 5194 6281
Mobile - 07845139072
Nice to have
- Cool looking features

```html
<!DOCTYPE html>
<html lang="en">
<head>
<meta charset="utf-8">
<title>Varkelt Construction Ltd – Business Card</title>
<link href="https://fonts.googleapis.com/css2?family=Exo+2:wght@400;600;700&display=swap" rel="stylesheet">
<style>
  :root {
    --stage: #8a8a8a;
    --card-white: #ffffff;
    --green-dark: #4b8c3f;
    --green-light: #76bd43;
    --ink: #4a4a4a;
    --white: #ffffff;
  }
  * { box-sizing: border-box; margin: 0; padding: 0; }
  html, body {
    width: 1125px; height: 1200px; overflow: hidden;
    background: var(--stage);
    font-family: "Exo 2", Arial, sans-serif;
  }
  .card {
    position: absolute; left: 171px; width: 826px; height: 471px;
  }
  /* Front */
  .card--front { top: 106px; background: var(--card-white); }
  .name-band {
    position: absolute; left: 0; top: 147px; width: 481px; height: 75px;
    background: var(--green-dark); color: var(--white);
    padding: 12px 0 0 40px;
  }
  .name-band__name { font-size: 27px; font-weight: 700; letter-spacing: 0.3px; line-height: 1.1; text-transform: uppercase; }
  .name-band__title { font-size: 16px; font-weight: 400; margin-top: 2px; }
  .brand {
    position: absolute; left: 490px; top: 130px; width: 306px;
    color: var(--green-light); font-weight: 700; text-align: right;
  }
  .brand__name { font-size: 70px; line-height: 0.95; letter-spacing: 1px; text-transform: uppercase; }
  .brand__sub { font-size: 19px; letter-spacing: 3.5px; text-transform: uppercase; margin-top: 2px; }
  .contact {
    position: absolute; top: 384px; font-size: 18px; color: var(--ink);
    list-style: none; line-height: 24px;
  }
  .contact li { display: flex; align-items: center; gap: 9px; }
  .contact--left { left: 43px; }
  .contact--right { right: 43px; font-size: 16px; top: 388px; }
  .contact--right li { justify-content: flex-end; }
  .icon { width: 14px; height: 14px; flex: none; }
  /* Back */
  .card--back { top: 640px; background: var(--green-dark); color: var(--white); }
  .back-brand {
    position: absolute; left: 0; right: 0; top: 150px; text-align: center;
    font-weight: 700; font-size: 64px; letter-spacing: 2px; text-transform: uppercase;
  }
  .rule { position: absolute; left: 141px; top: 278px; width: 518px; height: 3px; background: var(--white); }
  .services {
    position: absolute; left: 0; right: 0; top: 314px; text-align: center;
    font-size: 17px; line-height: 23.5px; font-weight: 400;
  }
  .tick { font-size: 16px; }
</style>
</head>
<body>
  <section class="card card--front">
    <div class="name-band">
      <p class="name-band__name">Tomasz Brelwik</p>
      <p class="name-band__title">Managing Director</p>
    </div>
    <div class="brand">
      <p class="brand__name">Varkelt</p>
      <p class="brand__sub">Construction Ltd</p>
    </div>
    <ul class="contact contact--left">
      <li>
        <svg class="icon" viewBox="0 0 16 16"><path fill="#76bd43" d="M3.5 1l2.5 3-1.5 1.8c.9 2 2.4 3.5 4.4 4.4L10.7 8.7l3 2.5-1.2 2.8C7 13.8 2 9 2 2.5z"/></svg>
        020 5194 6281
      </li>
      <li>
        <svg class="icon" viewBox="0 0 16 16"><rect x="4" y="1" width="8" height="14" rx="1.5" fill="#76bd43"/><rect x="5.5" y="3" width="5" height="8.5" fill="#fff"/></svg>
        07845139072
      </li>
    </ul>
    <ul class="contact contact--right">
      <li>tomasz@varkelt.co.uk
        <svg class="icon" viewBox="0 0 16 16"><rect x="1" y="3" width="14" height="10" fill="#76bd43"/><path d="M1.5 3.5L8 9l6.5-5.5" stroke="#fff" stroke-width="1.3" fill="none"/></svg>
      </li>
      <li>www.varkelt.co.uk
        <svg class="icon" viewBox="0 0 16 16"><circle cx="8" cy="8" r="7" fill="#76bd43"/><path d="M5 4c2 1 1 3 3 3s1 3 3 4M9 2.5c0 2 2 2 3.5 2" stroke="#fff" stroke-width="1.3" fill="none"/></svg>
      </li>
    </ul>
  </section>

  <section class="card card--back">
    <p class="back-brand">Varkelt</p>
    <div class="rule"></div>
    <p class="services">
      Kitchen Renovations <span class="tick">✓</span> Bathroom Renovations <span class="tick">✓</span> House Renovations<br>
      Garage Conversions <span class="tick">✓</span> Extensions <span class="tick">✓</span> Loft Conversions <span class="tick">✓</span> Conservatories<br>
      Carpentry <span class="tick">✓</span> Tiling <span class="tick">✓</span> Electrical <span class="tick">✓</span> Plumbing &amp; Heating <span class="tick">✓</span> Bricklaying<br>
      Landscaping <span class="tick">✓</span> Decorating <span class="tick">✓</span> Plastering
    </p>
  </section>
</body>
</html>
```